Update Powerpoint Presentation

We need to update the existing Powerpoint presentation to make it look more professional, less words and get the message across to potential clients. Our clients are banks and lenders in Australia.
Reason: To give the designers more time to come up with designs
Reason: I am looking for a design that is more innovative and doesn't just re-create what I gave. This presentation is only an example of what I would like I am keen to find a presentation that takes it to the next level.
It Professional

```html
<!DOCTYPE html>
<html lang="en">
<head>
<meta charset="utf-8">
<title>Service Offerings</title>
<link href="https://fonts.googleapis.com/css2?family=Carlito:ital,wght@0,400;0,700;1,700&display=swap" rel="stylesheet">
<style>
  :root {
    --navy: #1d3f7d;
    --intro-bg: #2b5283;
    --footer-bg: #0c3d6f;
    --tab: #1f4a7a;
    --panel: #ececec;
    --ribbon: #c9dff1;
    --ink: #2b2b2b;
    --bullet: #2e659f;
  }
  * { box-sizing: border-box; margin: 0; padding: 0; }
  html, body { width: 1200px; height: 900px; overflow: hidden; background: #ffffff; }
  body { font-family: "Carlito", "Calibri", Arial, sans-serif; color: var(--ink); position: relative; }

  .page-title {
    position: absolute; left: 38px; top: 66px;
    font-size: 27px; font-weight: 700; font-style: italic; color: var(--navy); line-height: 32px;
  }
  .title-rule { position: absolute; left: 282px; top: 89px; width: 758px; height: 1px; background: var(--navy); }
  .brand {
    position: absolute; right: 36px; top: 34px;
    font-size: 34px; font-weight: 700; color: var(--navy); line-height: 40px;
  }

  .intro {
    position: absolute; left: 40px; top: 104px; width: 1120px; height: 84px;
    background: var(--intro-bg); color: #fff;
    padding: 16px 30px 0; font-size: 18px; line-height: 26px;
    box-shadow: 0 5px 6px rgba(0,0,0,.3);
  }

  .diagram-heading {
    position: absolute; left: 30px; top: 208px;
    font-size: 18px; font-weight: 700; color: var(--navy); line-height: 22px;
  }

  .panel { position: absolute; left: 30px; width: 1160px; background: var(--panel); }
  .panel-new { top: 240px; height: 282px; }
  .panel-discharge { top: 545px; height: 282px; }
  .ribbon {
    position: absolute; left: 0; top: 0; width: 100%; height: 6px;
    background: linear-gradient(to right, var(--ribbon), #eaf3fb 60%, var(--ribbon));
  }
  .tab {
    position: absolute; left: 0; top: 0; width: 38px; height: 100%;
    background: var(--tab); color: #fff;
    display: flex; align-items: center; justify-content: center;
  }
  .tab span {
    writing-mode: vertical-rl; transform: rotate(180deg);
    font-size: 21px; font-weight: 700; letter-spacing: .5px;
  }

  .chevrons { position: absolute; left: 0; top: 0; width: 1200px; height: 900px; pointer-events: none; }

  .step-head {
    position: absolute; height: 52px; color: #fff;
    font-size: 14px; font-weight: 700; line-height: 16px;
    display: flex; align-items: center;
  }
  .step-list {
    position: absolute; list-style: none;
    font-size: 14px; line-height: 19px;
  }
  .step-list li { position: relative; padding-left: 13px; margin-bottom: 7px; }
  .step-list li::before {
    content: ""; position: absolute; left: 0; top: 7px;
    width: 6px; height: 6px; background: var(--bullet);
  }

  .divider { position: absolute; width: 1px; background: #c8c8c8; }

  .footer {
    position: absolute; left: 0; top: 858px; width: 1200px; height: 42px;
    background: var(--footer-bg); color: #fff; font-size: 19px;
  }
  .footer span { position: absolute; top: 10px; line-height: 22px; }
</style>
</head>
<body>

  <h1 class="page-title">SERVICE OFFERINGS</h1>
  <div class="title-rule"></div>
  <div class="brand">Harbourline</div>

  <p class="intro">“Mortgage Servicing” covers the full range of mortgage management and administration services a lender can outsource to a third party — from receipt of instructions to prepare documents through to repayment and discharge of the mortgage.</p>

  <h2 class="diagram-heading">THE DIAGRAM BELOW DETAILS THE SERVICES PROVIDED BY HARBOURLINE.</h2>

  <div class="panel panel-new"><div class="ribbon"></div><div class="tab"><span>New Loans</span></div></div>
  <div class="panel panel-discharge"><div class="ribbon"></div><div class="tab"><span>Discharges</span></div></div>

  <svg class="chevrons" viewBox="0 0 1200 900" aria-hidden="true">
    <g>
      <polygon fill="#173a6e" points="80,252 220,252 234,278 220,304 80,304"/>
      <polygon fill="#1f4a7f" points="237,252 377,252 391,278 377,304 237,304 251,278"/>
      <polygon fill="#275890" points="394,252 534,252 548,278 534,304 394,304 408,278"/>
      <polygon fill="#2e659f" points="551,252 691,252 705,278 691,304 551,304 565,278"/>
      <polygon fill="#3973ad" points="708,252 848,252 862,278 848,304 708,304 722,278"/>
      <polygon fill="#4680b9" points="865,252 1005,252 1019,278 1005,304 865,304 879,278"/>
      <polygon fill="#548dc4" points="1022,252 1162,252 1176,278 1162,304 1022,304 1036,278"/>
    </g>
    <g>
      <polygon fill="#173a6e" points="80,560 246,560 260,586 246,612 80,612"/>
      <polygon fill="#22508a" points="263,560 429,560 443,586 429,612 263,612 277,586"/>
      <polygon fill="#2c629c" points="446,560 612,560 626,586 612,612 446,612 460,586"/>
      <polygon fill="#3672aa" points="629,560 795,560 809,586 795,612 629,612 643,586"/>
      <polygon fill="#4380b8" points="812,560 978,560 992,586 978,612 812,612 826,586"/>
      <polygon fill="#548dc4" points="995,560 1161,560 1175,586 1161,612 995,612 1009,586"/>
    </g>
  </svg>

  <!-- New Loans -->
  <div class="step-head" style="left:90px; top:252px; width:130px;">Document Preparation</div>
  <div class="step-head" style="left:257px; top:252px; width:120px;">Verification</div>
  <div class="step-head" style="left:414px; top:252px; width:120px;">Bookings and Enquiries</div>
  <div class="step-head" style="left:571px; top:252px; width:120px;">Certification and Settlement Prep</div>
  <div class="step-head" style="left:728px; top:252px; width:120px;">Settlements</div>
  <div class="step-head" style="left:885px; top:252px; width:120px;">Stamping and Lodgement</div>
  <div class="step-head" style="left:1042px; top:252px; width:120px;">Custody</div>

  <div class="divider" style="left:235px; top:318px; height:190px;"></div>
  <div class="divider" style="left:392px; top:318px; height:190px;"></div>
  <div class="divider" style="left:549px; top:318px; height:190px;"></div>
  <div class="divider" style="left:706px; top:318px; height:190px;"></div>
  <div class="divider" style="left:863px; top:318px; height:190px;"></div>
  <div class="divider" style="left:1020px; top:318px; height:190px;"></div>

  <ul class="step-list" style="left:84px; top:320px; width:145px;">
    <li>File creation</li>
    <li>Title search</li>
    <li>Fee check</li>
    <li>Loan pack to borrower</li>
  </ul>
  <ul class="step-list" style="left:243px; top:320px; width:142px;">
    <li>Check execution and witnessing</li>
    <li>Chase incomplete documents</li>
  </ul>
  <ul class="step-list" style="left:400px; top:320px; width:142px;">
    <li>Book with solicitor / conveyancer</li>
    <li>Book with outgoing lender</li>
    <li>Log in settlement diary</li>
  </ul>
  <ul class="step-list" style="left:557px; top:320px; width:142px;">
    <li>Certify and request funds</li>
    <li>Confirm disbursements</li>
    <li>Issue cheques</li>
  </ul>
  <ul class="step-list" style="left:714px; top:320px; width:142px;">
    <li>Final search</li>
    <li>Collect bank cheques</li>
    <li>Attend and confirm settlement</li>
  </ul>
  <ul class="step-list" style="left:871px; top:320px; width:142px;">
    <li>Stamp documents</li>
    <li>Lodge with the LTO</li>
  </ul>
  <ul class="step-list" style="left:1028px; top:320px; width:142px;">
    <li>Receive documents from LTO</li>
    <li>Transfer to custodian</li>
  </ul>

  <!-- Discharges -->
  <div class="step-head" style="left:90px; top:560px; width:150px;">Document Preparation</div>
  <div class="step-head" style="left:283px; top:560px; width:146px;">Bookings and Enquiries</div>
  <div class="step-head" style="left:466px; top:560px; width:146px;">Advise Payout Figures</div>
  <div class="step-head" style="left:649px; top:560px; width:146px;">Prepare Settlement Instructions</div>
  <div class="step-head" style="left:832px; top:560px; width:146px;">Settlements</div>
  <div class="step-head" style="left:1015px; top:560px; width:146px;">Custody</div>

  <div class="divider" style="left:261px; top:626px; height:186px;"></div>
  <div class="divider" style="left:444px; top:626px; height:186px;"></div>
  <div class="divider" style="left:627px; top:626px; height:186px;"></div>
  <div class="divider" style="left:810px; top:626px; height:186px;"></div>
  <div class="divider" style="left:993px; top:626px; height:186px;"></div>

  <ul class="step-list" style="left:84px; top:628px; width:170px;">
    <li>File creation</li>
    <li>Fee check</li>
    <li>Discharge executed by attorney</li>
    <li>Letter to requesting party</li>
  </ul>
  <ul class="step-list" style="left:269px; top:628px; width:168px;">
    <li>Log in settlement diary</li>
  </ul>
  <ul class="step-list" style="left:452px; top:628px; width:168px;">
    <li>Obtain payout from outgoing lender</li>
    <li>Advise incoming lender</li>
  </ul>
  <ul class="step-list" style="left:635px; top:628px; width:168px;">
    <li>Forward to state office or settlement agent</li>
  </ul>
  <ul class="step-list" style="left:818px; top:628px; width:168px;">
    <li>Collect payout funds</li>
    <li>Deposit cheques</li>
  </ul>
  <ul class="step-list" style="left:1001px; top:628px; width:168px;">
    <li>Security packet to custodian</li>
  </ul>

  <footer class="footer">
    <span style="left:32px;">Commercial in Confidence</span>
    <span style="left:566px;">June 2013</span>
    <span style="right:22px;">Page-3</span>
  </footer>

</body>
</html>
```